Car transport business

We need a new business card design. Attached is our old card sample. I would just like to adjust the logo colors (blue and red) to be brighter. I changed my name to the brighter red and the word dispatcher to a brighter blue as an example. But you can adjust those colors further. And then perhaps you can use the same colors for the card design but use your imagination.

As a suggestion so the card stands out I would like to add a clip art of car carrier truck. Attached are examples of that as well

```html
<!DOCTYPE html>
<html lang="en">
<head>
<meta charset="utf-8">
<title>Swift Haul – Business Card</title>
<link rel="stylesheet" href="https://fonts.googleapis.com/css2?family=Montserrat:wght@400;500;700;800&display=swap">
<style>
  :root {
    --stage: #2b2c2e;
    --brand-blue: #1e78c8;
    --brand-blue-deep: #1a6ab3;
    --brand-red: #e8202a;
    --paper: #ffffff;
    --rule: #8a8a8a;
    --shadow: rgba(0, 0, 0, 0.55);
  }
  * { box-sizing: border-box; margin: 0; padding: 0; }
  html, body {
    width: 1200px;
    height: 1015px;
    overflow: hidden;
    background: var(--stage);
    font-family: "Montserrat", Arial, sans-serif;
  }
  .card {
    position: absolute;
    width: 560px;
    height: 320px;
    box-shadow: 0 14px 30px var(--shadow);
  }

  /* Back side */
  .card-back {
    left: 70px;
    top: 140px;
    background: var(--brand-blue);
    overflow: hidden;
  }
  .card-back .pattern {
    position: absolute;
    inset: 0;
    background: linear-gradient(135deg, #2583d4 0%, var(--brand-blue) 50%, var(--brand-blue-deep) 100%);
  }
  .card-back .wordmark {
    position: absolute;
    left: 150px;
    top: 230px;
    display: flex;
    align-items: center;
    gap: 12px;
  }
  .card-back .wordmark .dot {
    width: 30px;
    height: 30px;
    border-radius: 50%;
    background: var(--paper);
  }
  .card-back .wordmark .name {
    font-weight: 800;
    font-size: 34px;
    letter-spacing: 3px;
    color: var(--paper);
  }

  /* Front side */
  .card-front {
    left: 570px;
    top: 540px;
    background: var(--paper);
  }
  .card-front .brand {
    position: absolute;
    left: 150px;
    top: 58px;
    display: flex;
    align-items: center;
    gap: 14px;
  }
  .card-front .brand .dot {
    width: 40px;
    height: 40px;
    border-radius: 50%;
    background: var(--brand-blue);
  }
  .card-front .brand .name {
    font-weight: 800;
    font-size: 40px;
    letter-spacing: 3px;
    color: var(--brand-blue);
    line-height: 1;
  }
  .card-front .brand .tagline {
    display: block;
    font-weight: 500;
    font-size: 10.5px;
    letter-spacing: 3.4px;
    color: var(--brand-blue);
    margin-top: 6px;
    text-transform: uppercase;
  }
  .card-front .rule {
    position: absolute;
    left: 215px;
    right: 28px;
    top: 205px;
    height: 1px;
    background: var(--rule);
  }
  .card-front .person {
    position: absolute;
    left: 38px;
    top: 182px;
  }
  .card-front .person .full-name {
    font-weight: 500;
    font-size: 25px;
    letter-spacing: 0.5px;
    line-height: 1;
  }
  .card-front .person .first { color: var(--brand-blue); }
  .card-front .person .last { color: var(--brand-red); }
  .card-front .person .role {
    font-size: 12px;
    letter-spacing: 0.5px;
    color: var(--brand-blue);
    margin-top: 4px;
  }
  .card-front .contacts {
    position: absolute;
    left: 40px;
    top: 246px;
    list-style: none;
  }
  .card-front .contacts li {
    display: flex;
    align-items: center;
    gap: 10px;
    font-size: 14px;
    color: var(--brand-red);
    line-height: 21px;
  }
  .card-front .contacts svg {
    width: 14px;
    height: 14px;
    fill: var(--brand-blue);
    flex: none;
  }
</style>
</head>
<body>

<section class="card card-back" aria-label="Card back">
  <div class="pattern" role="img" aria-label="Repeating embossed pattern of the company emblem on blue"></div>
  <div class="wordmark">
    <span class="dot"></span>
    <span class="name">SWIFT HAUL</span>
  </div>
</section>

<section class="card card-front" aria-label="Card front">
  <div class="brand">
    <span class="dot"></span>
    <div>
      <span class="name">SWIFT HAUL</span>
      <span class="tagline">The Auto Transport Professionals</span>
    </div>
  </div>
  <div class="rule"></div>

  <div class="person">
    <div class="full-name"><span class="first">LEO</span> <span class="last">MARSH</span></div>
    <div class="role">DISPATCHER</div>
  </div>

  <ul class="contacts">
    <li>
      <svg viewBox="0 0 24 24" aria-hidden="true"><path d="M6.6 10.8a15.1 15.1 0 0 0 6.6 6.6l2.2-2.2a1 1 0 0 1 1-.25 11.4 11.4 0 0 0 3.6.57 1 1 0 0 1 1 1V20a1 1 0 0 1-1 1A17 17 0 0 1 3 4a1 1 0 0 1 1-1h3.5a1 1 0 0 1 1 1c0 1.25.2 2.45.57 3.57a1 1 0 0 1-.25 1z"/></svg>
      555-014-2287
    </li>
    <li>
      <svg viewBox="0 0 24 24" aria-hidden="true"><path d="M6 2h10v6H6zM4 9h16a2 2 0 0 1 2 2v7h-4v4H6v-4H2v-7a2 2 0 0 1 2-2zm4 7v4h8v-4z"/></svg>
      555-014-2290
    </li>
    <li>
      <svg viewBox="0 0 24 24" aria-hidden="true"><path d="M2 5h20v14H2zm2 2v.5l8 5.5 8-5.5V7l-8 5.5z"/></svg>
      swifthaulco@example.com
    </li>
  </ul>
</section>

</body>
</html>
```